Business card design for my company.
I would like the card's background colour to be black. You can also see our web site to get an idea of our brand. https://www.tmwhomecrafting.com.au/
- Name
- Email

```html
<!DOCTYPE html>
<html lang="en">
<head>
<meta charset="UTF-8">
<title>TMW Home Crafting – Business Card</title>
<link rel="stylesheet" href="https://fonts.googleapis.com/css2?family=Montserrat:wght@400;500;700&display=swap">
<style>
  :root {
    --stage: #3a3a3a;
    --card: #212121;
    --card-back: #1f1f1f;
    --green: #16994a;
    --white: #f4f4f4;
    --muted: #2b2b2b;
  }
  * { margin: 0; padding: 0; box-sizing: border-box; }
  html, body {
    width: 1200px; height: 875px; overflow: hidden;
    background: var(--stage);
    font-family: "Montserrat", Arial, sans-serif;
  }
  .canvas {
    position: relative; width: 1200px; height: 875px;
  }
  .card {
    position: absolute; left: 300px;
    width: 600px; height: 343px;
    border-radius: 22px;
    overflow: hidden;
  }
  .card-back {
    top: 70px;
    background: var(--card-back);
    display: flex; align-items: center; justify-content: center;
  }
  .back-wordmark {
    font-weight: 700; font-size: 40px; letter-spacing: 2px;
    color: var(--muted);
    text-transform: uppercase;
  }
  .card-front {
    top: 462px;
    background: var(--card);
    border-bottom: 9px solid var(--green);
  }
  .brand {
    position: absolute; top: 40px; right: 40px;
    display: flex; align-items: center; gap: 12px;
  }
  .brand-square {
    width: 22px; height: 22px; background: var(--green);
  }
  .brand-name {
    font-weight: 700; font-size: 22px; letter-spacing: 1px;
    color: var(--white); text-transform: uppercase;
  }
  .person {
    position: absolute; left: 48px; bottom: 44px;
  }
  .person-name {
    font-weight: 700; font-size: 26px; letter-spacing: 1px;
    color: var(--green); text-transform: uppercase;
  }
  .person-title {
    font-weight: 400; font-size: 17px; color: var(--white);
    margin-top: 2px;
  }
  .divider {
    width: 12px; height: 2px; background: var(--green);
    margin: 16px 0 12px;
  }
  .contact-list { list-style: none; }
  .contact-item {
    display: flex; align-items: center; gap: 10px;
    font-size: 16px; color: var(--white);
    line-height: 28px;
  }
  .contact-icon { width: 13px; height: 13px; flex: none; }
</style>
</head>
<body>
<main class="canvas">
  <section class="card card-back" aria-label="Card back">
    <span class="back-wordmark">TMW Home Crafting</span>
  </section>

  <section class="card card-front" aria-label="Card front">
    <div class="brand">
      <span class="brand-square"></span>
      <span class="brand-name">TMW Home Crafting</span>
    </div>

    <div class="person">
      <h1 class="person-name">Daniel Hayes</h1>
      <p class="person-title">CEO/Founder</p>
      <div class="divider"></div>
      <ul class="contact-list">
        <li class="contact-item">
          <svg class="contact-icon" viewBox="0 0 24 24"><path fill="#16994a" d="M6.6 10.8a15.2 15.2 0 0 0 6.6 6.6l2.2-2.2c.3-.3.7-.4 1-.2 1.1.4 2.3.6 3.6.6.6 0 1 .4 1 1V20c0 .6-.4 1-1 1A17 17 0 0 1 3 4c0-.6.4-1 1-1h3.5c.6 0 1 .4 1 1 0 1.3.2 2.5.6 3.6.1.3 0 .7-.2 1z"/></svg>
          897-555-0142
        </li>
        <li class="contact-item">
          <svg class="contact-icon" viewBox="0 0 24 24"><path fill="#16994a" d="M2 5h20v14H2z"/><path fill="none" stroke="#212121" stroke-width="2" d="M2 5l10 8 10-8"/></svg>
          info@tmwhomecrafting.com.au
        </li>
        <li class="contact-item">
          <svg class="contact-icon" viewBox="0 0 24 24"><circle cx="12" cy="12" r="10" fill="none" stroke="#16994a" stroke-width="2"/><path fill="none" stroke="#16994a" stroke-width="2" d="M2 12h20M12 2c3 3 3 17 0 20M12 2c-3 3-3 17 0 20"/></svg>
          www.tmwhomecrafting.com.au
        </li>
      </ul>
    </div>
  </section>
</main>
</body>
</html>
```